Folder and brochures for food service software solution

We offer integrated software solutions for independent and chain food service businesses. Such businesses would include fine dining restaurants, fast food outlets, home delivery, takeaways, cafeterias, event catering venues, institutional catering companies, hotels with restaurants / bars, etc. Our software is configured for the needs of each type of business and spans both guest facing and back office functions.

The core benefits our solution offers is that it is -
1. integrated to cater to all the needs of the food service business, both independent and chain, across most (not all, we do not do anything for labor management) functions.
2. functionally powerful and compare well with the best available internationally.
3. Developed using the latest in software technology ... for example, our EPOS software for Nimbus OS devices.

The market is a mature market with many competitors. A few very well established with huge track record. We have a track record internationally but are new to the UK market. This brochure is targeted at the UK market. The target market is jaded with the number of options available. We will focus on fine dining outlets in the hope that our Nimbus OS based EPOS will excite them. We will focus on events & catering because the competition in the segment is relatively thin. We will go after the institutional catering market because we offer strong cost control features. But we want to mention how we service all sub-segments of the food & beverage service business to convey the versatility of our solution and for the other businesses that we may be able to attract.

We are hoping that the brochure will stand-out from the crowd and will compel the market to browse through what we do.

Some key competitors in the UK include -
http://www.venbrook.co.uk/
http://www.q-til.co.uk/
http://www.harromax.co.uk/
http://dunvey.co.uk/

We have a company and product logo (both attached). Of these, we are open to dropping or redesgning the product logo. We have also developed a web site (see kbuk.tarvensystems.example). The brochure design need not conform to the web site, if (and only if) you can come up with a really attention design (we could consider redesign of the web site).

The content of the brochure will largely conform to the content at the web site. The content at the web site is structured by solutions for independent outlets (centered around the EPOS) and solutions for chains. It also mentions 18 products. This is too much for a print brochure. So, we propose the following structure -

1. a folder that also carries a brief about our company with facility to add inserts.
2. one brochure that describes the solutions offered, the market segments they apply to and the benefits of the solution for each segment.
3. A summary / list of the products that are used to configure the solution.

We will add product specific flyers to the folder by color laser printing these. This will provide us the flexibility to add only the few product sheets that are of relevance to each prospect and will allow us to update frequently. For this we will require a template so that all product sheets look similar ... possibly with a color theme separating the products for each outlet from those for the chain of outlets.

We can only provide low-res images. You will have to touch up screens to improve resolution of images to make them print-ready. You are free to propose purchase of reasonably priced general stock-shots subject to prior approval from us. We will pay for these images.
Updates

At least one of you have requested that we -

1. identify a key message and

2. compact the contents of the brochure 

To do so, we have had to take an alternative approach and revise the content completely. Please check back and see the latest uploads, both Marlo - Approach 2 and Marlo - Salient Features.

We hope this helps you in your design effort.                     

Reason: We understand that we are requesting this design through a holiday season. We are extending the deadline by a few days. If this also does not work for some of you, please let us know a realistic date by which you are able to provide us options. We will consider, even though we are on a tight time line.

Reason: Some of you are still working on final layouts At least one of you is waiting for us to provide you modified content to fit the design. The extra days are intended to allow you to provide a complete and final design.

Earlier, we had posted an update and new content. This was in response to the community's request to reduce content. Did you note that? It seems not. So, we have now removed older content and only retained the revised content as per the last update. Please verify that the design you propose is as per the latest content. In the process, we may have removed some images also. Need them? Let me know and I will re-post.

Reason: Further extension, open only to those that have previously submitted designs and need the extra time to finalize the design based on feedback from us.

Target Market(s)

Upper mid market fine dining restaurants, likely with home delivery / takeaway options.
Small food service chains (3 to 10 outlets).
Venues with catering facilities.
Cafeterias.
Bulk food suppliers / institutional caterers.
Food service business with a central kitchen / commissary and multiple service locations.
membership clubs with food service.

Industry/Entity Type

Software

Font styles to use
Sans Serif

Requirements
Must have
• A distinctive attention grabbing design.

The structure of -
1. a folder with facility for inserts.
2. two brochures.
3. template for product specific write-ups.
Nice to have
• Info-graphics to represent an integrated solution. Another to demonstrate versatility across types of F&B business.

A design that relates the solution to the UK ... either in terms of colors or visuals.

```html
<!DOCTYPE html>
<html lang="en">
<head>
<meta charset="utf-8">
<title>Marlo – Sector-specific benefits</title>
<link href="https://fonts.googleapis.com/css2?family=Open+Sans:ital,wght@0,400;0,700;1,600&display=swap" rel="stylesheet">
<style>
  :root {
    --brand-red: #c8102e;
    --brand-red-dark: #9e0b22;
    --ink: #3a3a3a;
    --paper: #ffffff;
  }
  * { box-sizing: border-box; margin: 0; padding: 0; }
  html, body { width: 843px; height: 1200px; overflow: hidden; background: var(--paper); }
  body { font-family: "Open Sans", Arial, sans-serif; color: var(--ink); }
  .page { position: relative; width: 843px; height: 1200px; overflow: hidden; }

  .banner {
    position: absolute; left: 0; top: 0; width: 843px; height: 150px;
    background: linear-gradient(180deg, var(--brand-red) 0%, var(--brand-red-dark) 100%);
    display: flex; align-items: center; justify-content: center;
    padding: 0 70px;
  }
  .banner h1 {
    color: var(--paper); font-style: italic; font-weight: 600;
    font-size: 27px; line-height: 1.25; text-align: center;
  }

  .sector { position: absolute; left: 0; width: 843px; }
  .sector-photo { position: absolute; left: 0; width: 252px; }
  .sector-body { position: absolute; left: 266px; right: 22px; top: 0; }
  .sector h2 {
    color: var(--brand-red); font-weight: 700; font-size: 29px;
    line-height: 1.1; margin-bottom: 6px;
  }
  .sector ul { list-style: none; }
  .sector li {
    position: relative; padding-left: 11px;
    font-size: 12.4px; line-height: 15.2px;
  }
  .sector li::before {
    content: ""; position: absolute; left: 0; top: 6px;
    width: 4px; height: 4px; border-radius: 50%; background: var(--ink);
  }

  .fine-dining { top: 168px; }
  .fine-dining .sector-photo { top: 0; height: 250px; background: linear-gradient(135deg, #e9e4dc, #a88f73 60%, #4b3a2c); }
  .hotels { top: 500px; }
  .hotels .sector-photo { top: -8px; height: 222px; background: linear-gradient(135deg, #6b4a36, #c9a98a 55%, #f1e7da); }
  .quick-service { top: 762px; }
  .quick-service .sector-photo { top: -10px; height: 232px; background: linear-gradient(135deg, #d8c2a4, #b26b3b 55%, #5a3322); }
  .food-courts { top: 1000px; }
  .food-courts .sector-photo { top: -6px; height: 206px; background: linear-gradient(135deg, #cfd3d6, #7a8a96 55%, #2e3a44); }

  .brand-mark {
    position: absolute; left: 600px; top: 1100px;
    color: var(--brand-red); font-weight: 700; font-size: 52px; line-height: 1;
  }
</style>
</head>
<body>
<div class="page">
  <header class="banner">
    <h1>Marlo can be configured specifically for each type of food service business. In each case, it offers additional sector-specific benefits.</h1>
  </header>

  <section class="sector fine-dining">
    <div class="sector-photo" role="img" aria-label="Chef plating a fine dining dish"></div>
    <div class="sector-body">
      <h2>Fine Dining</h2>
      <ul>
        <li>Table Reservations module that helps optimal use of available tables through meal times. The table reservation system can be interfaced with a 3rd party table reservations portal of your choice.</li>
        <li>Table status is monitored allowing for further efficiency in table management.</li>
        <li>A repeat diner database that is valuable for direct marketing, guest recognition, personalization of guest services and customer profiling. For example, it can automatically add the guest's known allergies to the KOT on the guest's repeat visit.</li>
        <li>Order taking features such as course wise order taking for timely food preparation and cover wise order taking for improved table service.</li>
        <li>Automated application of discounts and promotions for loyalty and/or dining members.</li>
        <li>Personalized order taking at the table side.</li>
      </ul>
    </div>
  </section>

  <section class="sector hotels">
    <div class="sector-photo" role="img" aria-label="Hotel restaurant interior with set tables"></div>
    <div class="sector-body">
      <h2>Hotels</h2>
      <ul>
        <li>Multi-outlet table reservations module that allows a guest to call a single number to book a table at any of the outlets in a hotel.</li>
        <li>In-room dining orders handling.</li>
        <li>Each POS station can handle multiple outlets.</li>
        <li>Take orders anywhere and print KOT instantly by using the cost-effective Nimbus OS mobile version of Marlo order taking.</li>
        <li>Add comments to the KOT so that Chef is informed about any special guest requests.</li>
        <li>Post checks to guest room account. Currently, Marlo is in use with Tarven Systems' HALO, Stayline and Innkeep PMSs. It can be interfaced with any PMS that supports FIAS or HTNG interface standards.</li>
      </ul>
    </div>
  </section>

  <section class="sector quick-service">
    <div class="sector-photo" role="img" aria-label="Friends sharing fast food at a table"></div>
    <div class="sector-body">
      <h2>Quick Service / Fast Food</h2>
      <ul>
        <li>Minimum key strokes for EPOS operations that makes guest handling fast.</li>
        <li>Point-of-purchase promotion through dual display at each EPOS station.</li>
        <li>More efficient food preparation by use of Kitchen Display Systems as alternative to KOT printers.</li>
        <li>Integration with loyalty system with instant redemption.</li>
        <li>Online inventory to track stocks of critical items and to initiate replenishment.</li>
      </ul>
    </div>
  </section>

  <section class="sector food-courts">
    <div class="sector-photo" role="img" aria-label="Cashless card payment at a food court counter"></div>
    <div class="sector-body">
      <h2>Food Courts</h2>
      <ul>
        <li>All the benefits of QSR service, plus the option of cashless operations.</li>
        <li>Aggregate sales of all outlets for multi-outlet and/or consolidated reporting.</li>
      </ul>
    </div>
  </section>

  <div class="brand-mark">Marlo</div>
</div>
</body>
</html>
```